BrivoTerna. Lantern of the Steady Harvest. Business card

Professional business card for BrivoTerna (Lantern of the Steady Harvest)
My rationale: Strategy-> Execution-> Results-> Value that lead to the BrivoTerna name: We put the Lantern of the Steady Harvest.
We deliver value to our customers helping them at defining a good strategy (cyan arrow). 90% of well formulated strategies fail due to poor execution so we also consider strategical execution very important (green arrow). Due to the execution we obtain the results (blue arrow). Finally, the results provide feedback to redefine strategy, and the new strategy has to be executed and new results obtained providing new feedback and on and on. It's like a wheel that finally, must create corporate value: value for shareholders, staholders, employees, providers...-

Target Market(s)

CEOs and steering comitees , invewrnent funds

Industry/Entity Type

Business Consultant

Contact Information for Business Card

Teodoro Vinsquel
CEO & Founder
teodoro.vinsquel@brivoterna-example.com
Mobile: +34 655.803.912
www.brivoterna-example.com

Colors

Designer to choose colors to be used in the design.

Requirements
Nice to have
• Nice to hace the words: Strategy, execution, results
• Nice to vave the claim: Lantern of the Steady Harvest
• The three colors should be shown:
• cyan for STRATEGY
• green for EXECUTION
• blue for RESULTS
Should not have
• Complete black background

```html
<!DOCTYPE html>
<html lang="en">
<head>
<meta charset="utf-8">
<title>BrivoTerna — Business Card</title>
<link rel="stylesheet" href="https://fonts.googleapis.com/css2?family=Open+Sans:wght@400;600;700;800&display=swap">
<style>
  :root {
    --navy: #0b3a96;
    --blue-deep: #06329a;
    --green: #8cc63f;
    --cyan: #1ba8e0;
    --ink-grey: #555a60;
    --paper: #ffffff;
    --backdrop: #dcd8d4;
    --rule: #5bc0eb;
  }
  * { margin: 0; padding: 0; box-sizing: border-box; }
  html, body {
    width: 1200px; height: 997px; overflow: hidden;
    background: var(--backdrop);
    font-family: "Open Sans", Arial, sans-serif;
  }
  .canvas {
    position: relative; width: 1200px; height: 997px;
  }
  .card {
    position: absolute; width: 700px; height: 400px;
    background: var(--paper);
    box-shadow: 0 6px 18px rgba(0,0,0,0.12);
    overflow: hidden;
  }
  .card--front { left: 250px; top: 70px; }
  .card--back  { left: 250px; top: 530px; }

  .card__art { position: absolute; inset: 0; width: 700px; height: 400px; }
  .pillar-label {
    font-family: "Open Sans", Arial, sans-serif;
    font-weight: 700; font-size: 15px; fill: #fff;
  }

  .brand {
    position: absolute; left: 56px; top: 118px;
    display: flex; align-items: center; gap: 10px;
  }
  .brand__mark { width: 22px; height: 22px; background: var(--cyan); }
  .brand__name {
    font-weight: 800; font-size: 38px; color: var(--navy);
    letter-spacing: -1px; line-height: 1;
  }

  .person { position: absolute; left: 58px; top: 196px; }
  .person__name { font-weight: 700; font-size: 20px; color: var(--navy); }
  .person__role { font-size: 15px; color: var(--ink-grey); margin-top: 1px; }

  .contacts { position: absolute; left: 58px; top: 268px; list-style: none; }
  .contacts li {
    display: flex; align-items: center; gap: 10px;
    font-size: 15px; color: var(--ink-grey); line-height: 25px;
  }
  .contacts svg { width: 14px; height: 14px; fill: var(--navy); flex: none; }

  .lockup {
    position: absolute; left: 0; right: 0; top: 130px;
    text-align: center;
  }
  .lockup__name {
    font-weight: 800; font-size: 78px; color: var(--navy);
    letter-spacing: -2px; line-height: 1;
  }
  .tagline {
    display: flex; align-items: center; justify-content: center;
    gap: 12px; margin-top: 18px;
  }
  .tagline__rule { width: 140px; height: 1px; background: var(--rule); }
  .tagline__text { font-size: 18px; color: var(--navy); }
</style>
</head>
<body>
<main class="canvas">

  <section class="card card--front" aria-label="Business card front">
    <svg class="card__art" viewBox="0 0 700 400" aria-hidden="false">
      <polygon class="panel" points="505,0 700,0 700,400 548,400" fill="var(--blue-deep)"/>
      <polygon points="470,42 700,42 700,76 462,76" fill="var(--blue-deep)"/>
      <polygon points="440,76 700,76 700,108 432,108" fill="var(--green)"/>
      <polygon points="410,108 700,108 700,140 402,140" fill="var(--cyan)"/>
      <text class="pillar-label" x="490" y="65">Results</text>
      <text class="pillar-label" x="460" y="98">Execution</text>
      <text class="pillar-label" x="428" y="130">Strategy</text>
    </svg>

    <div class="brand">
      <span class="brand__mark"></span>
      <span class="brand__name">BrivoTerna</span>
    </div>

    <div class="person">
      <div class="person__name">Teodoro Vinsquel</div>
      <div class="person__role">CEO &amp; Founder</div>
    </div>

    <ul class="contacts">
      <li>
        <svg viewBox="0 0 16 16" aria-hidden="true"><path d="M4 0h8a1 1 0 0 1 1 1v14a1 1 0 0 1-1 1H4a1 1 0 0 1-1-1V1a1 1 0 0 1 1-1zm1 2v10h6V2zm3 11a1 1 0 1 0 0 2 1 1 0 0 0 0-2z"/></svg>
        +34 655.803.912
      </li>
      <li>
        <svg viewBox="0 0 16 16" aria-hidden="true"><path d="M0 3h16v10H0zm1.5 1.3V12h13V4.3L8 9z"/><path d="M1 3h14L8 8z"/></svg>
        teodoro.vinsquel@brivoterna-example.com
      </li>
      <li>
        <svg viewBox="0 0 16 16" aria-hidden="true"><path d="M8 0a8 8 0 1 0 0 16A8 8 0 0 0 8 0zm-1 1.6V5H4.2A6.5 6.5 0 0 1 7 1.6zm2 0A6.5 6.5 0 0 1 11.8 5H9zM3.6 6.5H7v3H3.6a6.5 6.5 0 0 1 0-3zm5.4 0h3.4a6.5 6.5 0 0 1 0 3H9zM4.2 11H7v3.4A6.5 6.5 0 0 1 4.2 11zM9 11h2.8A6.5 6.5 0 0 1 9 14.4z"/></svg>
        www.brivoterna-example.com
      </li>
    </ul>
  </section>

  <section class="card card--back" aria-label="Business card back">
    <div class="lockup">
      <div class="lockup__name">BrivoTerna</div>
      <div class="tagline">
        <span class="tagline__rule"></span>
        <span class="tagline__text">Lantern of the Steady Harvest</span>
        <span class="tagline__rule"></span>
      </div>
    </div>
  </section>

</main>
</body>
</html>
```